Talon Microsystems PowerPoint Master Slide Deck Design

This is a 2-phase project to design a slide deck for a semiconductor company in the Silicon Valley. The design budget will be increased with each phase.
The slide deck will need to have one version with a dark background for presentations and a second version with a white background. Otherwise, the slides will be the same. I anticipate we will need a total of 10 slides, but that number may change.
The first phase will be to design a Title and a Title and Content slide.
- The Title Slide is the first slide of the deck. It should include the presentation title, the presenter's name and date of presentation
- The Title and Content slide should include a title and content with bullet points and up to 2 additional sub-bullets
- The Title and Content slide should have a footer that includes the slide #, Talon Microsystems Confidential, and the logo. This footer will be on every slide except the Title Slide
The first two slides will serve as the format for the remaining ~8 slides:
-Header and Content Text (1, 2, 4 column)
-Header and Content Image (bar chart, pie chart, tables)
-Break
-Title only
-Closing (Talon logo only)
Our slides contain a lot of content so a clean and simple design is best.
Both phases will need to include pre-set color options for
-Text and Lines
-Shadows
-Bullets and sub-bullets (including shapes, ex. circle, slash, square, etc.)
-Bar charts, pie charts, tables
Samples of our collateral are attached. Logo files are also attached
Look and feel
Each slider illustrates characteristics of the customer's brand and the style your logo design should communicate.

```html
<!DOCTYPE html>
<html lang="en">
<head>
<meta charset="utf-8">
<title>Talon Microsystems – Master Slide Deck</title>
<link href="https://fonts.googleapis.com/css2?family=Montserrat:wght@400;500;600;700&display=swap" rel="stylesheet">
<style>
:root{
  --blue:#1677e0;
  --blue-deep:#0b3fb8;
  --blue-soft:#39a0f5;
  --light-bg:#ecf6fd;
  --light-ink:#1d1f22;
  --light-muted:#3b3f45;
  --dark-bg:#111316;
  --dark-ink:#ffffff;
  --dark-muted:#d7dbe0;
  --sheet-bg:#ffffff;
}
*{margin:0;padding:0;box-sizing:border-box}
html,body{width:691px;height:1200px;overflow:hidden;background:var(--sheet-bg)}
body{font-family:"Montserrat",Arial,sans-serif}
.sheet{position:relative;width:1456px;height:2528px;transform:scale(0.4746);transform-origin:0 0}
.slide{position:absolute;width:709px;height:398px;overflow:hidden;background:var(--bg);color:var(--ink);
  --bg:var(--light-bg);--ink:var(--light-ink);--muted:var(--light-muted);--brand-ink:#3a3d42}
.slide--dark{--bg:var(--dark-bg);--ink:var(--dark-ink);--muted:var(--dark-muted);--brand-ink:#ffffff}
.col-l{left:14px}.col-r{left:735px}
.row1{top:14px}.row2{top:427px}.row3{top:837px}.row4{top:1250px}.row5{top:1663px}.row6{top:2082px}

/* backgrounds */
.slide--cover{background:linear-gradient(120deg,#e6eff8 0%,#f1f5fa 60%,#e2ecf6 100%)}
.slide--cover.slide--dark{background:linear-gradient(120deg,#0d151c 0%,#12181d 55%,#0a0e12 100%)}

/* brand */
.brand{position:absolute;display:flex;align-items:center;gap:6px;color:var(--brand-ink);font-weight:600;white-space:nowrap}
.brand-dot{border-radius:50%;border:3px solid var(--blue);flex:none}
.slide--dark .brand-dot{border-color:#fff}
.brand--corner{top:24px;right:16px;font-size:13px}
.brand--corner .brand-dot{width:16px;height:16px;border-width:2px}
.brand--footer{bottom:12px;left:50%;transform:translateX(-50%);font-size:8px;gap:4px}
.brand--footer .brand-dot{width:10px;height:10px;border-width:2px}
.brand--cover{top:34px;left:32px;font-size:24px;gap:10px}
.brand--cover .brand-dot{width:34px;height:34px;border-width:5px}
.brand--closing{top:50%;left:50%;transform:translate(-50%,-50%);font-size:46px;gap:20px}
.brand--closing .brand-dot{width:70px;height:70px;border-width:9px}

/* cover */
.cover-dash{position:absolute;left:32px;top:161px;width:50px;height:4px;background:var(--blue);border-radius:2px}
.cover-title{position:absolute;left:32px;top:178px;font-size:25px;line-height:26px;font-weight:600;width:300px}
.cover-by{position:absolute;left:32px;top:244px;font-size:12px;font-weight:500}
.cover-date{position:absolute;left:32px;top:265px;font-size:8px;color:var(--blue-soft)}
.cover-graphic{position:absolute;left:320px;top:60px;width:370px;height:320px;border-radius:50%;
  background:radial-gradient(circle at 50% 50%,rgba(22,119,224,.45) 0%,rgba(22,119,224,.15) 45%,rgba(22,119,224,0) 70%)}

/* header */
.slide-title{position:absolute;left:18px;top:18px;font-size:24px;line-height:26px;font-weight:600;width:340px;padding-left:0}
.title-bar{position:absolute;left:0;top:20px;width:4px;height:48px;background:var(--blue)}

/* footer */
.footer-note{position:absolute;left:18px;bottom:8px;font-size:6.5px;font-weight:500}
.footer-page{position:absolute;right:14px;bottom:8px;font-size:6.5px;font-weight:500}
.footer-band{position:absolute;left:0;right:0;bottom:0;height:4px;background:var(--blue)}

/* numbered list */
.point{position:absolute;width:320px;height:80px}
.point-num{position:absolute;left:0;top:-8px;font-size:62px;line-height:70px;font-weight:700;
  background:linear-gradient(180deg,var(--blue-soft),var(--blue-deep));-webkit-background-clip:text;background-clip:text;color:transparent}
.point-head{position:absolute;left:44px;top:0;font-size:12.5px;font-weight:600}
.point-list{position:absolute;left:44px;top:21px;list-style:none;font-size:7px;line-height:12.5px;color:var(--muted)}
.point-list li{position:relative;padding-left:11px;white-space:nowrap}
.point-list li::before{content:"";position:absolute;left:0;top:2.5px;width:5px;height:5px;border-radius:50%;background:var(--blue);box-shadow:0 0 0 1.5px var(--bg),0 0 0 2.5px var(--blue)}

/* text column */
.text-col{position:absolute;width:300px;text-align:right}
.text-head{font-size:12.5px;font-weight:600}
.text-rule{display:block;margin:6px 0 22px auto;width:30px;height:3px;border-radius:2px;background:var(--blue)}
.text-body{font-size:6.9px;line-height:12.6px;color:var(--muted);text-align:right}

/* image */
.image-frame{position:absolute;left:382px;top:90px;width:292px;height:200px;background:var(--blue)}
.image-fill{position:absolute;left:370px;top:102px;width:293px;height:200px;
  background:radial-gradient(circle at 50% 45%,#cfe0ff 0%,#6e8df0 22%,#2f4fc4 48%,#14288a 80%,#0c1d63 100%)}

/* chart */
.bar-chart{position:absolute;left:72px;top:110px}
</style>
</head>
<body>
<div class="sheet">

  <!-- Row 1: Title slides -->
  <section class="slide slide--cover col-l row1">
    <div class="brand brand--cover"><span class="brand-dot"></span>Talon Microsystems</div>
    <div class="cover-graphic" role="img" aria-label="Large blue brand graphic"></div>
    <div class="cover-dash"></div>
    <h1 class="cover-title">Lorem Ipsum is simply dummy</h1>
    <p class="cover-by">By Elena Marsh</p>
    <p class="cover-date">December 2023</p>
  </section>
  <section class="slide slide--cover slide--dark col-r row1">
    <div class="brand brand--cover"><span class="brand-dot"></span>Talon Microsystems</div>
    <div class="cover-graphic" role="img" aria-label="Large blue brand graphic"></div>
    <div class="cover-dash"></div>
    <h1 class="cover-title">Lorem Ipsum is simply dummy</h1>
    <p class="cover-by">By Elena Marsh</p>
    <p class="cover-date">December 2023</p>
  </section>

  <!-- Row 2: Title and content -->
  <section class="slide col-l row2">
    <div class="title-bar"></div>
    <h2 class="slide-title">Lorem Ipsum is simply dummy</h2>
    <div class="brand brand--corner"><span class="brand-dot"></span>Talon</div>
    <div class="point" style="left:18px;top:93px"><span class="point-num">1</span><h3 class="point-head">Lorem Ipsum</h3><ul class="point-list"><li>Wafer yield improved across all fabs this quarter</li><li>Process node roadmap remains on schedule</li><li>Packaging costs fell as volumes grew</li></ul></div>
    <div class="point" style="left:18px;top:181px"><span class="point-num">2</span><h3 class="point-head">Lorem Ipsum</h3><ul class="point-list"><li>Wafer yield improved across all fabs this quarter</li><li>Process node roadmap remains on schedule</li><li>Packaging costs fell as volumes grew</li></ul></div>
    <div class="point" style="left:18px;top:268px"><span class="point-num">3</span><h3 class="point-head">Lorem Ipsum</h3><ul class="point-list"><li>Wafer yield improved across all fabs this quarter</li><li>Process node roadmap remains on schedule</li><li>Packaging costs fell as volumes grew</li></ul></div>
    <div class="point" style="left:362px;top:93px"><span class="point-num">4</span><h3 class="point-head">Lorem Ipsum</h3><ul class="point-list"><li>Wafer yield improved across all fabs this quarter</li><li>Process node roadmap remains on schedule</li><li>Packaging costs fell as volumes grew</li></ul></div>
    <div class="point" style="left:362px;top:181px"><span class="point-num">5</span><h3 class="point-head">Lorem Ipsum</h3><ul class="point-list"><li>Wafer yield improved across all fabs this quarter</li><li>Process node roadmap remains on schedule</li><li>Packaging costs fell as volumes grew</li></ul></div>
    <div class="point" style="left:362px;top:268px"><span class="point-num">6</span><h3 class="point-head">Lorem Ipsum</h3><ul class="point-list"><li>Wafer yield improved across all fabs this quarter</li><li>Process node roadmap remains on schedule</li><li>Packaging costs fell as volumes grew</li></ul></div>
    <p class="footer-note">Talon Microsystems Confidential</p>
    <div class="brand brand--footer"><span class="brand-dot"></span>Talon</div>
    <p class="footer-page">Page No 2</p>
    <div class="footer-band"></div>
  </section>
  <section class="slide slide--dark col-r row2">
    <div class="title-bar"></div>
    <h2 class="slide-title">Lorem Ipsum is simply dummy</h2>
    <div class="brand brand--corner"><span class="brand-dot"></span>Talon</div>
    <div class="point" style="left:18px;top:93px"><span class="point-num">1</span><h3 class="point-head">Lorem Ipsum</h3><ul class="point-list"><li>Wafer yield improved across all fabs this quarter</li><li>Process node roadmap remains on schedule</li><li>Packaging costs fell as volumes grew</li></ul></div>
    <div class="point" style="left:18px;top:181px"><span class="point-num">2</span><h3 class="point-head">Lorem Ipsum</h3><ul class="point-list"><li>Wafer yield improved across all fabs this quarter</li><li>Process node roadmap remains on schedule</li><li>Packaging costs fell as volumes grew</li></ul></div>
    <div class="point" style="left:18px;top:268px"><span class="point-num">3</span><h3 class="point-head">Lorem Ipsum</h3><ul class="point-list"><li>Wafer yield improved across all fabs this quarter</li><li>Process node roadmap remains on schedule</li><li>Packaging costs fell as volumes grew</li></ul></div>
    <div class="point" style="left:362px;top:93px"><span class="point-num">4</span><h3 class="point-head">Lorem Ipsum</h3><ul class="point-list"><li>Wafer yield improved across all fabs this quarter</li><li>Process node roadmap remains on schedule</li><li>Packaging costs fell as volumes grew</li></ul></div>
    <div class="point" style="left:362px;top:181px"><span class="point-num">5</span><h3 class="point-head">Lorem Ipsum</h3><ul class="point-list"><li>Wafer yield improved across all fabs this quarter</li><li>Process node roadmap remains on schedule</li><li>Packaging costs fell as volumes grew</li></ul></div>
    <div class="point" style="left:362px;top:268px"><span class="point-num">6</span><h3 class="point-head">Lorem Ipsum</h3><ul class="point-list"><li>Wafer yield improved across all fabs this quarter</li><li>Process node roadmap remains on schedule</li><li>Packaging costs fell as volumes grew</li></ul></div>
    <p class="footer-note">Talon Microsystems Confidential</p>
    <div class="brand brand--footer"><span class="brand-dot"></span>Talon</div>
    <p class="footer-page">Page No 2</p>
    <div class="footer-band"></div>
  </section>

  <!-- Row 3: Two columns -->
  <section class="slide col-l row3">
    <div class="title-bar"></div>
    <h2 class="slide-title">Lorem Ipsum is simply dummy</h2>
    <div class="brand brand--corner"><span class="brand-dot"></span>Talon</div>
    <div class="text-col" style="left:38px;top:110px"><h3 class="text-head">Lorem Ipsum</h3><span class="text-rule"></span><p class="text-body">Our design teams delivered first silicon on the new low power platform ahead of plan. Test results show strong margins across voltage and temperature corners. Customer sampling starts next quarter, with volume ramp targeted for the second half. Supply agreements with foundry partners are in place, and capacity has been reserved to support demand through the coming year and beyond.</p></div>
    <div class="text-col" style="left:377px;top:110px"><h3 class="text-head">Lorem Ipsum</h3><span class="text-rule"></span><p class="text-body">Our design teams delivered first silicon on the new low power platform ahead of plan. Test results show strong margins across voltage and temperature corners. Customer sampling starts next quarter, with volume ramp targeted for the second half. Supply agreements with foundry partners are in place, and capacity has been reserved to support demand through the coming year and beyond.</p></div>
    <p class="footer-note">Talon Microsystems Confidential</p>
    <div class="brand brand--footer"><span class="brand-dot"></span>Talon</div>
    <p class="footer-page">Page No 3</p>
    <div class="footer-band"></div>
  </section>
  <section class="slide slide--dark col-r row3">
    <div class="title-bar"></div>
    <h2 class="slide-title">Lorem Ipsum is simply dummy</h2>
    <div class="brand brand--corner"><span class="brand-dot"></span>Talon</div>
    <div class="text-col" style="left:38px;top:110px"><h3 class="text-head">Lorem Ipsum</h3><span class="text-rule"></span><p class="text-body">Our design teams delivered first silicon on the new low power platform ahead of plan. Test results show strong margins across voltage and temperature corners. Customer sampling starts next quarter, with volume ramp targeted for the second half. Supply agreements with foundry partners are in place, and capacity has been reserved to support demand through the coming year and beyond.</p></div>
    <div class="text-col" style="left:377px;top:110px"><h3 class="text-head">Lorem Ipsum</h3><span class="text-rule"></span><p class="text-body">Our design teams delivered first silicon on the new low power platform ahead of plan. Test results show strong margins across voltage and temperature corners. Customer sampling starts next quarter, with volume ramp targeted for the second half. Supply agreements with foundry partners are in place, and capacity has been reserved to support demand through the coming year and beyond.</p></div>
    <p class="footer-note">Talon Microsystems Confidential</p>
    <div class="brand brand--footer"><span class="brand-dot"></span>Talon</div>
    <p class="footer-page">Page No 3</p>
    <div class="footer-band"></div>
  </section>

  <!-- Row 4: Text and image -->
  <section class="slide col-l row4">
    <div class="title-bar"></div>
    <h2 class="slide-title">Lorem Ipsum is simply dummy</h2>
    <div class="brand brand--corner"><span class="brand-dot"></span>Talon</div>
    <div class="text-col" style="left:38px;top:110px"><h3 class="text-head">Lorem Ipsum</h3><span class="text-rule"></span><p class="text-body">Our design teams delivered first silicon on the new low power platform ahead of plan. Test results show strong margins across voltage and temperature corners. Customer sampling starts next quarter, with volume ramp targeted for the second half. Supply agreements with foundry partners are in place, and capacity has been reserved to support demand through the coming year and beyond.</p></div>
    <div class="image-frame"></div>
    <div class="image-fill" role="img" aria-label="Photo of a microchip on a glowing blue circuit board"></div>
    <p class="footer-note">Talon Microsystems Confidential</p>
    <div class="brand brand--footer"><span class="brand-dot"></span>Talon</div>
    <p class="footer-page">Page No 4</p>
    <div class="footer-band"></div>
  </section>
  <section class="slide slide--dark col-r row4">
    <div class="title-bar"></div>
    <h2 class="slide-title">Lorem Ipsum is simply dummy</h2>
    <div class="brand brand--corner"><span class="brand-dot"></span>Talon</div>
    <div class="text-col" style="left:38px;top:110px"><h3 class="text-head">Lorem Ipsum</h3><span class="text-rule"></span><p class="text-body">Our design teams delivered first silicon on the new low power platform ahead of plan. Test results show strong margins across voltage and temperature corners. Customer sampling starts next quarter, with volume ramp targeted for the second half. Supply agreements with foundry partners are in place, and capacity has been reserved to support demand through the coming year and beyond.</p></div>
    <div class="image-frame"></div>
    <div class="image-fill" role="img" aria-label="Photo of a microchip on a glowing blue circuit board"></div>
    <p class="footer-note">Talon Microsystems Confidential</p>
    <div class="brand brand--footer"><span class="brand-dot"></span>Talon</div>
    <p class="footer-page">Page No 4</p>
    <div class="footer-band"></div>
  </section>

  <!-- Row 5: Chart and text -->
  <section class="slide col-l row5">
    <div class="title-bar"></div>
    <h2 class="slide-title">Lorem Ipsum is simply dummy</h2>
    <div class="brand brand--corner"><span class="brand-dot"></span>Talon</div>
    <svg class="bar-chart" width="216" height="190" viewBox="0 0 216 190" font-family="Montserrat, Arial, sans-serif" font-size="8" font-weight="600" fill="#fff" text-anchor="middle">
      <rect x="4" y="101" width="35" height="77" fill="#2aa0e0"/><text x="21.5" y="113">40%</text>
      <rect x="39" y="44" width="35" height="134" fill="#17b39b"/><text x="56.5" y="56">70%</text>
      <rect x="74" y="120" width="35" height="58" fill="#8dc63f"/><text x="91.5" y="132">30%</text>
      <rect x="109" y="63" width="35" height="115" fill="#4a4a4a"/><text x="126.5" y="75">60%</text>
      <rect x="144" y="24" width="35" height="154" fill="#b05ee8"/><text x="161.5" y="36">80%</text>
      <rect x="179" y="5" width="35" height="173" fill="#f47a30"/><text x="196.5" y="17">90%</text>
      <g font-size="3.5" font-weight="500"><text x="21.5" y="172">Label</text><text x="56.5" y="172">Label</text><text x="91.5" y="172">Label</text><text x="126.5" y="172">Label</text><text x="161.5" y="172">Label</text><text x="196.5" y="172">Label</text></g>
    </svg>
    <div class="text-col" style="left:362px;top:128px"><h3 class="text-head">Lorem Ipsum</h3><span class="text-rule"></span><p class="text-body">Our design teams delivered first silicon on the new low power platform ahead of plan. Test results show strong margins across voltage and temperature corners. Customer sampling starts next quarter, with volume ramp targeted for the second half. Supply agreements with foundry partners are in place, and capacity has been reserved to support demand through the coming year and beyond.</p></div>
    <p class="footer-note">Talon Microsystems Confidential</p>
    <div class="brand brand--footer"><span class="brand-dot"></span>Talon</div>
    <p class="footer-page">Page No 5</p>
    <div class="footer-band"></div>
  </section>
  <section class="slide slide--dark col-r row5">
    <div class="title-bar"></div>
    <h2 class="slide-title">Lorem Ipsum is simply dummy</h2>
    <div class="brand brand--corner"><span class="brand-dot"></span>Talon</div>
    <svg class="bar-chart" width="216" height="190" viewBox="0 0 216 190" font-family="Montserrat, Arial, sans-serif" font-size="8" font-weight="600" fill="#fff" text-anchor="middle">
      <rect x="4" y="101" width="35" height="77" fill="#2aa0e0"/><text x="21.5" y="113">40%</text>
      <rect x="39" y="44" width="35" height="134" fill="#17b39b"/><text x="56.5" y="56">70%</text>
      <rect x="74" y="120" width="35" height="58" fill="#8dc63f"/><text x="91.5" y="132">30%</text>
      <rect x="109" y="63" width="35" height="115" fill="#4a4a4a"/><text x="126.5" y="75">60%</text>
      <rect x="144" y="24" width="35" height="154" fill="#b05ee8"/><text x="161.5" y="36">80%</text>
      <rect x="179" y="5" width="35" height="173" fill="#f47a30"/><text x="196.5" y="17">90%</text>
      <g font-size="3.5" font-weight="500"><text x="21.5" y="172">Label</text><text x="56.5" y="172">Label</text><text x="91.5" y="172">Label</text><text x="126.5" y="172">Label</text><text x="161.5" y="172">Label</text><text x="196.5" y="172">Label</text></g>
    </svg>
    <div class="text-col" style="left:362px;top:128px"><h3 class="text-head">Lorem Ipsum</h3><span class="text-rule"></span><p class="text-body">Our design teams delivered first silicon on the new low power platform ahead of plan. Test results show strong margins across voltage and temperature corners. Customer sampling starts next quarter, with volume ramp targeted for the second half. Supply agreements with foundry partners are in place, and capacity has been reserved to support demand through the coming year and beyond.</p></div>
    <p class="footer-note">Talon Microsystems Confidential</p>
    <div class="brand brand--footer"><span class="brand-dot"></span>Talon</div>
    <p class="footer-page">Page No 5</p>
    <div class="footer-band"></div>
  </section>

  <!-- Row 6: Closing -->
  <section class="slide slide--cover col-l row6">
    <div class="brand brand--closing"><span class="brand-dot"></span>Talon Microsystems</div>
  </section>
  <section class="slide slide--cover slide--dark col-r row6">
    <div class="brand brand--closing"><span class="brand-dot"></span>Talon Microsystems</div>
  </section>

</div>
</body>
</html>
```